Business Card Design for company

We want new business cards. We'd like something different-- yet still highly professional. Our tagline is Providing leadership, delivering success. Stock photos are ok, as long as they are relevant and look upscale.

Target Market(s)

Architecture/Business Management Consulting/Engineering Consulting

Contact Information for Business Card

dark gray background with pops of blue might be good, but you tell me. You're the designers. Rounded corners might be nice, but again, you tell me.

Font styles to use
Serif
Sans Serif

Colors
3276b5
5c5c5c
9d9d9d
fbfbfb

Requirements
Nice to have
• Something different, but still very professional.

```html
<!DOCTYPE html>
<html lang="en">
<head>
<meta charset="utf-8">
<title>Norvale Group — Business Card</title>
<link rel="stylesheet" href="https://fonts.googleapis.com/css2?family=Open+Sans:wght@300;400;600&display=swap">
<style>
  :root {
    --blue: #3276b5;
    --blue-light: #6fb3d6;
    --ink: #5c5c5c;
    --ink-dark: #2e2e2e;
    --gray-mid: #9d9d9d;
    --paper: #ffffff;
    --backdrop: #fbfbfb;
    --faint: #eef2f6;
  }
  * { margin: 0; padding: 0; box-sizing: border-box; }
  html, body { width: 1200px; height: 1023px; overflow: hidden; background: var(--backdrop); }
  body { display: flex; align-items: center; justify-content: center; font-family: "Open Sans", Arial, sans-serif; }

  .card {
    position: relative;
    width: 1050px;
    height: 600px;
    background: var(--paper);
    overflow: hidden;
    box-shadow: 0 2px 12px rgba(0,0,0,0.12);
  }
  .watermark {
    position: absolute;
    right: 40px;
    top: 40px;
    font-size: 120px;
    font-weight: 600;
    letter-spacing: 6px;
    color: var(--faint);
    line-height: 1;
  }
  .brand {
    position: absolute;
    left: 70px;
    top: 80px;
    display: flex;
    align-items: center;
    gap: 16px;
  }
  .brand-square { width: 34px; height: 34px; background: var(--blue); }
  .brand-name {
    font-size: 48px;
    font-weight: 600;
    color: var(--ink);
    letter-spacing: 2px;
  }
  .person { position: absolute; left: 200px; top: 185px; }
  .person-name { font-size: 34px; font-weight: 400; color: var(--ink-dark); }
  .person-role { font-size: 24px; font-weight: 300; color: var(--ink); }

  .contacts { position: absolute; left: 140px; top: 295px; list-style: none; }
  .contacts li {
    display: flex; align-items: center; gap: 16px;
    font-size: 22px; color: var(--ink-dark); height: 38px;
  }
  .contacts svg { width: 22px; height: 22px; flex: none; }

  .band { position: absolute; left: 0; bottom: 0; width: 1050px; height: 140px; }
</style>
</head>
<body>
  <div class="card">
    <div class="watermark" aria-hidden="true">NORVALE</div>

    <div class="brand">
      <span class="brand-square"></span>
      <span class="brand-name">Norvale Group</span>
    </div>

    <div class="person">
      <p class="person-name">Daniel Mercer</p>
      <p class="person-role">Owner</p>
    </div>

    <ul class="contacts">
      <li>
        <svg viewBox="0 0 22 22"><rect width="22" height="22" rx="3" fill="#6fa3d0"/><path d="M7 5l3 3-1.5 1.5a8 8 0 0 0 4 4L14 12l3 3-2 2C10 17 5 12 5 7z" fill="#fff"/></svg>
        +0000-0000-0000
      </li>
      <li>
        <svg viewBox="0 0 22 22"><rect width="22" height="22" rx="3" fill="#6fa3d0"/><rect x="5" y="7" width="12" height="9" fill="none" stroke="#fff" stroke-width="1.5"/><path d="M5 7l6 5 6-5" fill="none" stroke="#fff" stroke-width="1.5"/></svg>
        info@yourdomain.com
      </li>
      <li>
        <svg viewBox="0 0 22 22"><rect width="22" height="22" rx="3" fill="#6fa3d0"/><circle cx="11" cy="11" r="6" fill="none" stroke="#fff" stroke-width="1.5"/><path d="M5 11h12M11 5c-3 3-3 9 0 12M11 5c3 3 3 9 0 12" fill="none" stroke="#fff" stroke-width="1.2"/></svg>
        www.yourdomain.com
      </li>
      <li>
        <svg viewBox="0 0 22 22"><rect width="22" height="22" rx="3" fill="#6fa3d0"/><path d="M11 4a5 5 0 0 1 5 5c0 4-5 9-5 9s-5-5-5-9a5 5 0 0 1 5-5z" fill="#fff"/><circle cx="11" cy="9" r="2" fill="#6fa3d0"/></svg>
        Suite 210, 48 Harlow Lane, Bristol
      </li>
    </ul>

    <svg class="band" viewBox="0 0 1050 140" preserveAspectRatio="none" aria-hidden="true">
      <defs>
        <linearGradient id="bandBlue" x1="0" x2="1" y1="0" y2="0">
          <stop offset="0" stop-color="#6fb3d6"/>
          <stop offset="0.5" stop-color="#3276b5"/>
          <stop offset="1" stop-color="#2a68a3"/>
        </linearGradient>
        <linearGradient id="bandGray" x1="0" x2="1" y1="0" y2="0">
          <stop offset="0" stop-color="#5c5c5c"/>
          <stop offset="1" stop-color="#3a3a3a"/>
        </linearGradient>
      </defs>
      <rect x="0" y="0" width="1050" height="140" fill="url(#bandBlue)"/>
      <path d="M0 34 H560 L600 14 H640 V140 H0 Z" fill="#fff"/>
      <path d="M0 40 H562 L602 20 H640 V140 H0 Z" fill="url(#bandGray)"/>
    </svg>
  </div>
</body>
</html>
```